Brazilian-Italian food blogger looks for a yummy design for her blog

Ciao everyone! I am looking for a brand new design for my Wordpress food blog, MaRuPAN (marupan.net). The blog is about my deep love with food and with Bologna. I write particularly for the Brazilian crowd.
I talk about gastronomic curiosities of the town, delicious places and specialties that one can only find here. There are also many posts about my trips around Italy.
I would like the new design to be more sophisticated (or should I say professional?), but friendly at the same time.
If possible, I would like to keep its background very clean (if there are patters related to food, like the way it is now, even better), especially because I post many big colourful photos...
Also, since it is a personal blog, I would love if visitors could see a picture of mine and with a short description right at the homepage.
Thank you so much in advance.
Cheers,
Teresa.

Target Market(s)

Brazilian people interested in Italian culture and gastronomy.

Colors
fcca95

Requirements
Must have
• A neutral background that does not interfere with photos.
• My photo with a short description on the homepage.
Nice to have
• A background that has something to do with food.
Should not have
• It should not look like a girly blog.

```html
<!DOCTYPE html>
<html lang="en">
<head>
<meta charset="utf-8">
<title>MaRuPAN – My deep love with food</title>
<link href="https://fonts.googleapis.com/css2?family=Quicksand:wght@500;700&family=Open+Sans:wght@400;600&display=swap" rel="stylesheet">
<style>
:root{
  --page-bg:#f4f1eb;
  --paper:#ffffff;
  --brand:#c9772c;
  --brand-title:#d9822f;
  --nav:#f7c18f;
  --nav-active:#e3a16a;
  --ink:#555555;
  --ink-dark:#3a3a3a;
  --ink-soft:#7a7a7a;
  --line:#e3e3e3;
  --footer:#2e2e2e;
  --hero:#1c2535;
}
*{box-sizing:border-box;margin:0;padding:0}
html,body{width:1200px;height:2529px;overflow:hidden}
body{position:relative;background:var(--page-bg);font-family:"Open Sans",Arial,sans-serif;color:var(--ink)}
.pattern{position:absolute;inset:0;background:linear-gradient(90deg,#efe9df 0,#f4f1eb 50%,#efe9df 100%)}
.sheet{position:absolute;left:162px;top:0;width:880px;height:2431px;background:var(--paper);border-left:3px dashed #d9d9d9;border-right:3px dashed #d9d9d9}
.abs{position:absolute}
.site-name{left:222px;top:44px;font-family:"Open Sans",sans-serif;font-weight:600;font-size:28px;color:var(--ink-dark);letter-spacing:2px;text-transform:uppercase}
.search{left:780px;top:44px;width:215px;height:31px;border:1px solid #cfcfcf;font-size:12px;color:#999;padding:7px 10px}
.search svg{position:absolute;right:8px;top:8px}
.nav{left:202px;top:97px;width:795px;height:49px;background:var(--nav);display:flex;align-items:center}
.nav a{font-family:"Open Sans",sans-serif;font-size:13px;color:#fff;text-decoration:none;padding:0 19px;height:49px;line-height:49px}
.nav a.active{background:var(--nav-active)}
.hero{left:202px;top:146px;width:795px;height:364px;background:radial-gradient(ellipse at 50% 50%,#2c3850 0,var(--hero) 70%)}
.hero-title{left:202px;top:262px;width:795px;text-align:center;font-family:"Quicksand",sans-serif;font-weight:500;font-size:36px;color:#fff;letter-spacing:1px}
.hero-sub{left:202px;top:332px;width:795px;text-align:center;font-size:16px;color:#fff;letter-spacing:1px}
.hero-sub::before,.hero-sub::after{content:"";display:inline-block;width:90px;height:1px;background:#fff;vertical-align:middle;margin:0 16px}
.hero-arrow{top:310px;width:36px;height:36px;border-radius:50%;background:#c97a35}
.dots{left:570px;top:479px;display:flex;gap:4px}
.dots i{width:12px;height:12px;border-radius:50%;background:#bbb}
.dots i.on{background:#fff}
.card{left:188px;width:500px;border:1px solid var(--line);background:#fff}
.card h2{position:absolute;left:12px;top:22px;font-family:"Quicksand",sans-serif;font-weight:700;font-size:17px;color:var(--brand-title);text-transform:uppercase}
.card .photo{position:absolute;left:13px;top:67px;width:460px;height:182px}
.card p{position:absolute;left:13px;top:275px;width:462px;font-size:11.5px;line-height:16px;color:var(--ink-soft)}
.card .meta{position:absolute;left:13px;top:358px;width:460px;height:34px;border-top:1px solid var(--line);border-bottom:3px solid #222;display:flex;align-items:center;font-size:11px;color:var(--ink-soft);padding:0 14px;gap:26px}
.card .meta .date{margin-left:auto}
.meta span{display:flex;align-items:center;gap:5px}
.box{left:740px;width:268px;border:1px solid var(--line);background:#fff}
.box h3,.side-title{font-family:"Quicksand",sans-serif;font-weight:700;font-size:19px;color:var(--brand-title);text-transform:uppercase}
.about h3{text-align:center;margin-top:20px}
.avatar{position:absolute;left:66px;top:61px;width:135px;height:135px;border-radius:50%;background:radial-gradient(circle at 50% 40%,#d9a57c,#8a5a36)}
.about p{position:absolute;left:24px;top:218px;width:220px;text-align:center;font-size:11.5px;line-height:18px;color:var(--ink-soft)}
.social .name{position:absolute;left:18px;top:22px;font-family:"Open Sans",sans-serif;font-weight:600;font-size:14px;color:var(--ink-dark);letter-spacing:1px;text-transform:uppercase}
.social .small{font-size:10.5px;color:#444}
.faces{left:18px;top:95px;display:grid;grid-template-columns:repeat(6,30px);gap:4px}
.faces i{height:30px;background:#b9a38c}
.faces i:nth-child(odd){background:#8f9aa8}
.latest h3{position:absolute;left:14px;top:24px}
.item{position:absolute;left:14px;width:240px;height:56px}
.item .thumb{position:absolute;left:0;top:0;width:80px;height:56px;background:linear-gradient(135deg,#b88255,#6d4b36)}
.item b{position:absolute;left:96px;top:0;font-weight:400;font-size:13px;color:var(--brand-title)}
.item small{position:absolute;left:96px;top:20px;width:150px;font-size:11px;line-height:15px;color:var(--ink-soft)}
.archives{left:740px;top:1542px}
.archives ul{list-style:none;margin-top:14px}
.archives li{font-size:12.5px;color:var(--ink-soft);height:31px;padding-left:26px;position:relative}
.archives li::before{content:"";position:absolute;left:2px;top:5px;border-left:6px solid #888;border-top:4px solid transparent;border-bottom:4px solid transparent}
.gallery{left:14px;top:78px;display:grid;grid-template-columns:repeat(3,72px);gap:10px 13px}
.gallery i{height:57px;background:linear-gradient(135deg,#d98a45,#7d3d20)}
.gallery i:nth-child(3n+2){background:linear-gradient(135deg,#e0b070,#b05a2a)}
.gallery i:nth-child(n+7){background:linear-gradient(135deg,#9a6f7d,#3f5a88)}
.newsletter h3{position:absolute;left:12px;top:14px}
.field{position:absolute;left:12px;top:57px;width:146px;height:31px;background:#fde2c5;font-size:11px;color:#c58c5d;padding:8px 10px}
.btn{position:absolute;left:158px;top:57px;width:96px;height:31px;background:var(--brand);color:#fff;font-size:12px;font-weight:600;text-align:center;line-height:31px}
.pager{left:512px;top:2383px;display:flex;gap:3px}
.pager i{width:13px;height:14px;background:#e6e6e6;border:1px solid #cfcfcf}
.pager i.on{background:#bbb}
.footer{left:0;top:2431px;width:1200px;height:98px;background:var(--footer)}
.footer .links{position:absolute;left:208px;top:24px;font-size:12px;color:#eee}
.footer .copy{position:absolute;left:208px;top:56px;font-size:12px;color:#eee}
.icons{position:absolute;left:768px;top:35px;display:flex;gap:15px}
.icons i{width:28px;height:28px;border-radius:3px}
</style>
</head>
<body>
<div class="pattern" role="img" aria-label="Repeating pattern of forks, knives and spoons"></div>
<div class="sheet"></div>

<div class="abs site-name">MaRuPAN</div>
<div class="abs search">Search..
  <svg width="14" height="14" viewBox="0 0 14 14"><circle cx="6" cy="6" r="4.5" fill="none" stroke="#888" stroke-width="1.6"/><line x1="9.3" y1="9.3" x2="13" y2="13" stroke="#888" stroke-width="1.8"/></svg>
</div>

<nav class="abs nav">
  <a class="active">HOME</a><a>I, TERESA</a><a>THE BLOG</a><a>BELLA BO</a><a>CULINARY CONFESSIONS</a><a>BUONI POSTI</a><a>CONTACT</a>
</nav>

<div class="abs hero" role="img" aria-label="Overhead photo of a dark table with bread, herbs, spices and a teapot"></div>
<div class="abs hero-title">MY DEEP LOVE WITH FOOD</div>
<div class="abs hero-sub">OFFICIAL BLOG PAGE</div>
<div class="abs hero-arrow" style="left:202px"><svg width="36" height="36"><path d="M21 11 L14 18 L21 25" fill="none" stroke="#fff" stroke-width="2"/></svg></div>
<div class="abs hero-arrow" style="left:961px"><svg width="36" height="36"><path d="M15 11 L22 18 L15 25" fill="none" stroke="#fff" stroke-width="2"/></svg></div>
<div class="abs dots"><i class="on"></i><i></i><i></i><i></i></div>

<article class="abs card" style="top:566px;height:425px">
  <h2>Quisque sagittis semper felis, in condimentum</h2>
  <div class="photo" role="img" aria-label="Platter of sushi and sashimi" style="background:linear-gradient(135deg,#3a3a3a,#c9653a 60%,#6b4a2d)"></div>
  <p>Duis autem vel eum iriure dolor in hendreritvulputate velit esse molestie consequat, vill um dolore eu feugiat nulla facilisis at vero eros accumsan et iusto odio dignissim qui blan dpraesent luptatum zzril delenit augue duisdolore te feugait nulla facilisi.</p>
  <div class="meta"><span>READ MORE</span><span>22 OCT</span><span>&#9679; 1</span><span>&#9829; 34</span><span class="date">15 April 2014</span></div>
</article>

<article class="abs card" style="top:1020px;height:420px">
  <h2>Quisque sass, in condimentum</h2>
  <div class="photo" role="img" aria-label="Seafood stew in a dark pot with lemon" style="background:linear-gradient(135deg,#2c2c2c,#7a6a5a 50%,#c7713a)"></div>
  <p>Duis autem vel eum iriure dolor in hendreritvulputate velit esse molestie consequat, vill um dolore eu feugiat nulla facilisis at vero eros accumsan et iusto odio dignissim qui blan dpraesent luptatum zzril delenit augue duisdolore te feugait nulla facilisi.</p>
  <div class="meta"><span>READ MORE</span><span>22 OCT</span><span>&#9679; 1</span><span>&#9829; 34</span><span class="date">15 April 2014</span></div>
</article>

<article class="abs card" style="top:1479px;height:414px">
  <h2>Quisque sagittis semper felis, in condimentum</h2>
  <div class="photo" role="img" aria-label="Pastry parcels on a white plate with basil" style="background:linear-gradient(135deg,#8a2030,#e7d6bf 45%,#c99a6a)"></div>
  <p>Duis autem vel eum iriure dolor in hendreritvulputate velit esse molestie consequat, vill um dolore eu feugiat nulla facilisis at vero eros accumsan et iusto odio dignissim qui blan dpraesent luptatum zzril delenit augue duisdolore te feugait nulla facilisi.</p>
  <div class="meta"><span>READ MORE</span><span>22 OCT</span><span>&#9679; 1</span><span>&#9829; 34</span><span class="date">15 April 2014</span></div>
</article>

<article class="abs card" style="top:1928px;height:425px">
  <h2>Quisque sagittis semper felis, in condimentum</h2>
  <div class="photo" role="img" aria-label="Shrimp with saffron rice and greens" style="background:linear-gradient(135deg,#3f6a2a,#d9a23a 50%,#b74a2a)"></div>
  <p>Duis autem vel eum iriure dolor in hendreritvulputate velit esse molestie consequat, vill um dolore eu feugiat nulla facilisis at vero eros accumsan et iusto odio dignissim qui blan dpraesent luptatum zzril delenit augue duisdolore te feugait nulla facilisi.</p>
  <div class="meta"><span>READ MORE</span><span>22 OCT</span><span>&#9679; 1</span><span>&#9829; 34</span><span class="date">15 April 2014</span></div>
</article>

<div class="abs pager"><i class="on"></i><i></i><i></i><i></i><i></i><i></i><i></i><i></i><i></i><i style="margin-left:8px"></i></div>

<aside>
  <section class="abs box about" style="top:566px;height:324px">
    <h3>About me</h3>
    <div class="avatar" role="img" aria-label="Portrait photo of the blogger"></div>
    <p>Claritas est etiam processus dynamicus, qui sequitur mutationem consuetudium lectorum. Mirum est notare quam littera gothica</p>
  </section>

  <section class="abs box social" style="top:922px;height:207px">
    <div class="name">MaRuPAN</div>
    <div class="abs small" style="left:130px;top:16px">MaRuPAN</div>
    <div class="abs" style="left:130px;top:36px;width:40px;height:14px;border:1px solid #9aa7c2;background:#eef1f7"></div>
    <div class="abs small" style="left:18px;top:68px">30 people likes MaRuPAN</div>
    <div class="abs faces" role="img" aria-label="Grid of follower profile photos"><i></i><i></i><i></i><i></i><i></i><i></i><i></i><i></i><i></i><i></i><i></i><i></i></div>
    <div class="abs small" style="left:18px;top:180px;font-size:9.5px;color:#666">&#9632; Circlet Plugin Login</div>
  </section>

  <section class="abs box latest" style="top:1169px;height:340px">
    <h3>Latest articles</h3>
    <div class="item" style="top:78px"><div class="thumb" role="img" aria-label="Rooftops of Bologna"></div><b>Nam liber tempouut</b><small>Typi non habent claritatt m; est usius legentis qua.</small></div>
    <div class="item" style="top:159px"><div class="thumb" role="img" aria-label="Colourful street arcade"></div><b>Nam liber tempoumt</b><small>Typi non habent claritatt m; est usius legentis qua.</small></div>
    <div class="item" style="top:240px"><div class="thumb" role="img" aria-label="Piazza at dusk"></div><b>Nam liber tempoului</b><small>Typi non habent claritatt m; est usius legentis qua.</small></div>
  </section>

  <section class="abs archives">
    <div class="side-title">Archives</div>
    <ul>
      <li>January 2013 (123)</li><li>February 2013</li><li>March 2013</li><li>April 2013</li><li>May 2013</li><li>June 2013</li><li>July 2014</li><li>August 2014</li>
    </ul>
  </section>

  <section class="abs box" style="top:1851px;height:299px">
    <h3 class="abs" style="left:14px;top:26px">Snapgrid</h3>
    <div class="abs gallery" role="img" aria-label="Grid of food and city photos"><i></i><i></i><i></i><i></i><i></i><i></i><i></i><i></i><i></i></div>
  </section>

  <section class="abs box newsletter" style="top:2181px;height:115px">
    <h3>Newsletter signup</h3>
    <div class="field">Email ID</div>
    <div class="btn">SUBSCRIBE</div>
  </section>
</aside>

<footer class="abs footer">
  <div class="links">Terms and Conditions | Privacy Promise | FAQ's | Contact Us</div>
  <div class="copy">Copyright © 2013. All Rights Reserved.</div>
  <div class="icons"><i style="background:#3b5a9a"></i><i style="background:#3a9ad9"></i><i style="background:#f07a1e"></i><i style="background:#d8322a"></i><i style="background:#b0665a"></i></div>
</footer>
</body>
</html>
```